VKT Consulting

Government/Entitlement Consulting Services- I assist developers obtain entitlements from local, state and federal government agencies so that they can build their projects. Often these projects are very complicated and political and may face community opposition.

Target Market(s)

Real Estate Developers

Industry/Entity Type

Business Consultant

Contact Information for Business Card

Dana Melbrook
Principal

Font styles to use
Serif
Sans Serif

Requirements
Must have
• Classy and professional appeal.
Nice to have
• I like a combination of a mat and glossy finish. I've seen that done with black and then a bold color for a pop, but am not 100% committed to that.

```html
<!DOCTYPE html>
<html lang="en">
<head>
<meta charset="utf-8">
<title>VKT Consulting – Business Card</title>
<link href="https://fonts.googleapis.com/css2?family=Lato:wght@400;700&family=Libre+Baskerville:wght@700&display=swap" rel="stylesheet">
<style>
  :root {
    --stage: #e9e6e3;
    --frost: #f6f4f3;
    --frost-edge: #dcd8d5;
    --brand-red: #960808;
    --ink-light: #ffffff;
    --ghost: rgba(150, 8, 8, 0.18);
  }
  * { margin: 0; padding: 0; box-sizing: border-box; }
  html, body {
    width: 1200px; height: 900px; overflow: hidden;
    background: var(--stage);
    font-family: "Lato", sans-serif;
  }
  .stage { position: relative; width: 1200px; height: 900px; }

  .card {
    position: absolute;
    display: flex; flex-direction: column;
    box-shadow: 0 6px 18px rgba(0,0,0,0.12);
  }
  .card--front { left: 238px; top: 62px; width: 555px; height: 343px; }
  .card--back  { left: 459px; top: 518px; width: 560px; height: 343px; }

  .card__frost {
    background: var(--frost);
    border: 1px solid var(--frost-edge);
    border-bottom: none;
    display: flex; align-items: center; justify-content: center;
  }
  .card--front .card__frost { height: 185px; }
  .card--back  .card__frost { height: 187px; }

  .card__band {
    flex: 1;
    background: var(--brand-red);
    color: var(--ink-light);
  }

  .wordmark {
    display: flex; flex-direction: column; align-items: center;
    font-family: "Libre Baskerville", serif;
    font-weight: 700;
    color: var(--brand-red);
    text-transform: uppercase;
  }
  .wordmark__main { font-size: 80px; line-height: 80px; letter-spacing: 4px; }
  .wordmark__sub  { font-size: 27px; line-height: 32px; letter-spacing: 1px; margin-top: 4px; }
  .wordmark--ghost { color: var(--ghost); }

  .contact-row {
    display: flex; align-items: center;
    padding: 44px 0 0 26px;
    font-size: 15px; line-height: 20px;
  }
  .person { width: 152px; }
  .person__name { font-weight: 700; font-size: 18px; line-height: 22px; }
  .person__title { font-size: 15px; }

  .divider { width: 1px; height: 52px; background: rgba(255,255,255,0.75); }

  .address { padding: 0 10px 0 11px; width: 151px; }

  .channels { padding-left: 8px; list-style: none; }
  .channels li { display: flex; align-items: center; gap: 9px; }
  .channels svg { width: 11px; height: 11px; fill: var(--ink-light); flex: none; }

  .band__site {
    text-align: center;
    padding-top: 72px;
    font-size: 15px;
  }
</style>
</head>
<body>
<main class="stage">

  <section class="card card--front" aria-label="Card front">
    <div class="card__frost">
      <p class="wordmark" aria-label="VKT Consulting">
        <span class="wordmark__main">VKT</span>
        <span class="wordmark__sub">Consulting</span>
      </p>
    </div>
    <div class="card__band">
      <div class="contact-row">
        <div class="person">
          <p class="person__name">Dana Melbrook</p>
          <p class="person__title">Principal</p>
        </div>
        <span class="divider"></span>
        <p class="address">4820, Harbor Lane Westfield County, 482019.</p>
        <span class="divider"></span>
        <ul class="channels">
          <li>
            <svg viewBox="0 0 24 24" aria-hidden="true"><path d="M6.6 10.8a15.1 15.1 0 0 0 6.6 6.6l2.2-2.2a1 1 0 0 1 1-.25 11.4 11.4 0 0 0 3.6.57 1 1 0 0 1 1 1V20a1 1 0 0 1-1 1A17 17 0 0 1 3 4a1 1 0 0 1 1-1h3.5a1 1 0 0 1 1 1c0 1.25.2 2.45.57 3.57a1 1 0 0 1-.25 1z"/></svg>
            044-987 654 321
          </li>
          <li>
            <svg viewBox="0 0 24 24" aria-hidden="true"><path d="M2 5h20v14H2z M3.5 6.5 12 13l8.5-6.5" stroke="#960808" stroke-width="1.6"/></svg>
            info@vktconsult.com
          </li>
          <li>
            <svg viewBox="0 0 24 24" aria-hidden="true"><circle cx="12" cy="12" r="10"/><path d="M2 12h20M12 2c3 3 3 17 0 20M12 2c-3 3-3 17 0 20" stroke="#960808" stroke-width="1.4" fill="none"/></svg>
            www.vktconsult.com
          </li>
        </ul>
      </div>
    </div>
  </section>

  <section class="card card--back" aria-label="Card back">
    <div class="card__frost">
      <p class="wordmark wordmark--ghost" aria-label="VKT Consulting">
        <span class="wordmark__main">VKT</span>
        <span class="wordmark__sub">Consulting</span>
      </p>
    </div>
    <div class="card__band">
      <p class="band__site">www.vktconsult.com</p>
    </div>
  </section>

</main>
</body>
</html>
```